Kelvo bottle Label (Yoghurt drink)

Label for a 300 ml yoghurt drink bottle in 3 flavours.

General description:
• This is to design a sleeve shrink label for a Yoghurt Drink bottle in three flavours, Classic, Strawberry and Blueberry.
• Attached 3 photos: The one with KELVO brand in the current design we want to replace using the same bottle.
• Graphically, the design is to be similar to the examples provided for drumelo and fizzcrate.
• Use font and barcode size to be readable and legal.
• Minimize the use of the upper third of the bottle as it will be distorted when the label shrinks to the bottle.
• Professional and experienced designers only are welcome, please do not waste your time otherwise.

Bottle dimensions:
• Base across: 61 mm
• Height: 145 mm (approximate)

Graphical description:
• White colour with bands at the top and bottom similar to the one in “drumelo” example provided (not necessarily identical, feel free to be creative.
• The upper and lower bands to be: Green for “classic”, Pink or red for strawberry and purple for blueberry flavour.
• On the front: the brand name “Kelvo” and description “Yoghurt Drink” to be graphically attractive.
• On the front: two or more pieces of strawberry or blueberry for each flavour placed nicely with the option to include “yoghurt splash” or any suitable affects you deem suitable.
• For the Classic flavour, use the words (Classic, Lassi, Ayran) in the same location for the berries done in a graphically suitable manner.
• Colour temperature for the three flavours to be similar.

Information and objects on the label:
Front:
• The word “Kelvo” (brand name)
• “Yoghurt drink” (Product description)
• “300 ml” (size)
• Picture of Strawberries for strawberry flavour.
• Picture of Blueberries for blueberry flavour.
• The words (Classic, Lassi, Ayran) in the place used for the strawberries in the flavoured type, distributed to look graphically suitable for the overall design.

Back:
• Ingredient: Milk/milk solids, culture, salt, water, sugar, colour, flavour. (this is to be finalized later)
• Nutrition information table: (to be provided later).
• Barcode (to be provided later)
• Product of Australia
• Morel Tunsley Pty Ltd, 5/14 Ferrit St, Malaga, WA 6090
• info@kelvo-example.com.au 0491 000 372
• Keep under 5⁰ C
• Best before date printed on the bottle
• Shake well (to be located on the side at the top)
• Recycle icon.

Health benefits: (to be located suitably, possibly on the side with vertical orientation)
• Rich in probiotic bacteria and vitamins.
• Improves digestion and bowel motion.
• Supports weight control and fat loss.

Target Market(s)

General consumers

Industry/Entity Type

Grocery Store

Font styles to use
Sans Serif

Colors
abd037
b768aa
f04a50

Requirements
Must have
• The details in the project description
• The design must be simple and neat.
• Please use the shape of the current bottle "Kelvo" as in the attached photo.
Should not have
• Busy, cluttered, or empty and incomplete designs.

```html
<!DOCTYPE html>
<html lang="en">
<head>
<meta charset="utf-8">
<title>Kelvo Yogurt Drink – Blueberry Label</title>
<link rel="stylesheet" href="https://fonts.googleapis.com/css2?family=Fredoka:wght@600;700&display=swap">
<style>
  :root {
    --purple: #7f2d8f;
    --magenta: #a93c97;
    --lilac: #b58ac4;
    --pink: #e6207f;
    --orange: #f0662f;
    --splash-light: #eee2f1;
    --splash-mid: #d9c3e2;
    --berry: #3f5186;
    --white: #ffffff;
  }
  html, body {
    margin: 0;
    padding: 0;
    width: 1072px;
    height: 1200px;
    overflow: hidden;
    background: var(--white);
  }
  .label {
    display: block;
    width: 1072px;
    height: 1200px;
  }
  .title-yogurt {
    font-family: "Fredoka", sans-serif;
    font-weight: 700;
    fill: var(--purple);
  }
  .title-drink {
    font-family: "Fredoka", sans-serif;
    font-weight: 700;
    fill: var(--pink);
  }
  .brand-name {
    font-family: "Fredoka", sans-serif;
    font-weight: 700;
    fill: var(--purple);
    letter-spacing: 2px;
  }
</style>
</head>
<body>
<svg class="label" viewBox="0 0 1072 1200" xmlns="http://www.w3.org/2000/svg">
  <defs>
    <linearGradient id="dropGrad" x1="0" y1="1" x2="1" y2="0">
      <stop offset="0" stop-color="var(--pink)"/>
      <stop offset="1" stop-color="var(--orange)"/>
    </linearGradient>
    <radialGradient id="splashGrad" cx="0.5" cy="0.45" r="0.55">
      <stop offset="0" stop-color="var(--berry)"/>
      <stop offset="0.35" stop-color="#6a78a8"/>
      <stop offset="0.6" stop-color="var(--splash-mid)"/>
      <stop offset="1" stop-color="var(--splash-light)" stop-opacity="0"/>
    </radialGradient>
  </defs>

  <g class="band band-top">
    <path d="M261 0 H890 C720 30 420 80 261 349 Z" fill="var(--purple)"/>
    <path d="M330 0 H890 C720 40 440 110 300 300 C360 150 380 60 330 0 Z" fill="var(--magenta)" opacity="0.85"/>
    <path d="M700 0 H890 C820 18 760 30 700 40 Z" fill="var(--lilac)"/>
  </g>

  <g class="band band-bottom">
    <path d="M927 751 V1200 H153 C520 1150 860 1040 927 751 Z" fill="var(--purple)"/>
    <path d="M927 751 V860 C860 1080 560 1140 240 1200 H153 C520 1150 860 1040 927 751 Z" fill="var(--magenta)"/>
    <path d="M153 1200 C260 1170 360 1150 420 1140 L470 1200 Z" fill="var(--lilac)" opacity="0.8"/>
  </g>

  <rect role="img" aria-label="Pink and orange splash drops" x="434" y="72" width="176" height="113" rx="56" fill="url(#dropGrad)" transform="rotate(-30 522 128)" opacity="0.9"/>
  <rect role="img" aria-label="Pink and orange splash drops" x="474" y="980" width="233" height="100" rx="50" fill="url(#dropGrad)" transform="rotate(-25 590 1030)" opacity="0.9"/>

  <text class="brand-name" x="656" y="218" font-size="44" text-anchor="middle">KELVO</text>

  <text class="title-yogurt" x="0" y="0" font-size="180" text-anchor="middle" textLength="544" lengthAdjust="spacingAndGlyphs" transform="translate(460 624) rotate(-90)">Yogurt</text>
  <text class="title-drink" x="0" y="0" font-size="52" text-anchor="middle" textLength="128" lengthAdjust="spacingAndGlyphs" transform="translate(550 424) rotate(-90)">Drink</text>

  <ellipse role="img" aria-label="Blueberries with leaves in a yogurt splash" cx="790" cy="620" rx="260" ry="230" fill="url(#splashGrad)"/>
</svg>
</body>
</html>
```